Flat bootstrap design for existing site

I'm looking for a modern flat design based around an existing logo. This has to be a custom design (no external templates), and implemented into a bootstrap framework.

The logo is attached as 2 versions - choose whichever you want, that flows better with whatever design you choose.

Added screenshots of the existing site (currently using the default bootstrap layouts). Please make your designs around those pages in the screenshots (i.e. the homepage only has the postal code input and the header). The active page has 3 screenshots, because I wanted to illustrate the other states that would be visible (in the table rows).

This is a moving/junk removal website, just for some context.

Here's some example websites (flat designs) that I like, just to give you an idea of what I'm after.

https://www.plimvora.com/
https://dacklow.com/
https://trevanu.com/
https://quobrintal.com/en/

Coding

Coded - Design and coding required

Number of Pages Required

5+ page

Colors

Designer to choose colors to be used in the design.

Requirements
Must have
• It must be a modern/simple flat design, that is built around the existing logo (attached).
• It has to be implemented using bootstrap.

```html
<!DOCTYPE html>
<html lang="en">
<head>
<meta charset="utf-8">
<title>Haulbrix – Booking</title>
<link rel="stylesheet" href="https://fonts.googleapis.com/css2?family=Open+Sans:wght@400;600;700&display=swap">
<style>
  :root {
    --sky: #3fbdf1;
    --sky-dark: #2aa3da;
    --navy: #1b2140;
    --page: #f2f2f2;
    --white: #ffffff;
    --ink: #333333;
    --border: #bdbdbd;
    --notice-bg: #e8f3fa;
    --notice-ink: #3b5d74;
    --table-head: #159cea;
    --row: #ececec;
    --badge: #666666;
  }
  * { box-sizing: border-box; margin: 0; padding: 0; }
  html, body { width: 1200px; height: 649px; overflow: hidden; }
  body {
    font-family: "Open Sans", Arial, sans-serif;
    background: var(--page);
    color: var(--ink);
    position: relative;
  }
  .site-header {
    height: 70px;
    background: var(--sky);
    display: flex;
    align-items: center;
    padding: 0 21px;
  }
  .brand {
    display: flex; align-items: center; gap: 8px;
    color: var(--white); font-weight: 700; font-size: 22px; letter-spacing: 0.5px;
  }
  .brand-dot { width: 12px; height: 12px; border-radius: 50%; background: var(--white); }
  .main-nav { margin-left: auto; display: flex; align-items: center; }
  .main-nav a {
    color: var(--white); text-decoration: none; font-size: 13.5px;
    padding: 0 21px; line-height: 34px;
  }
  .main-nav a.nav-cta { background: var(--sky-dark); border-radius: 2px; margin: 0 8px; }
  .main-nav a.nav-account { padding-right: 0; }

  .panel { position: absolute; left: 22px; width: 1156px; background: var(--white); }
  .panel-title {
    background: var(--navy); color: var(--white);
    height: 42px; line-height: 42px; padding: 0 20px;
    font-size: 17.5px; font-weight: 600;
  }
  .booking { top: 99px; height: 147px; }
  .booking-form { display: flex; gap: 14px; padding: 24px 20px 0 20px; }
  .field label { display: block; font-size: 11.5px; margin-bottom: 7px; }
  .field .control {
    height: 36px; border: 1px solid var(--border); background: var(--white);
    display: flex; align-items: center; justify-content: space-between;
    padding: 0 13px; font-size: 10px;
  }
  .field-package { width: 226px; }
  .field-time { width: 226px; }
  .field-desc { width: 544px; }
  .btn-update {
    align-self: flex-end; width: 78px; height: 36px; border: 0;
    background: var(--sky); color: var(--white);
    font-family: inherit; font-weight: 600; font-size: 14px; letter-spacing: 0.5px;
  }

  .drivers { top: 268px; height: 330px; }
  .drivers-body { padding: 21px; }
  .notice {
    background: var(--notice-bg); color: var(--notice-ink);
    height: 49px; line-height: 49px; padding: 0 20px; font-size: 11.5px;
  }
  .driver-table { width: 100%; border-collapse: collapse; margin-top: 15px; font-size: 10.5px; }
  .driver-table th {
    background: var(--table-head); color: var(--white); font-weight: 400;
    font-size: 11.5px; text-align: left; height: 35px; padding: 0 0 0 20px;
  }
  .driver-table td {
    background: var(--row); height: 37px; padding: 0 0 0 20px;
    border-top: 2px solid var(--white);
  }
  .col-name { width: 189px; }
  .col-distance { width: 190px; }
  .col-time { width: 438px; }
  .status {
    display: inline-block; width: 97px; height: 21px; line-height: 21px;
    text-align: center; background: var(--badge); color: var(--white); font-size: 10px;
  }
  .site-footer {
    position: absolute; top: 617px; left: 0; width: 1200px;
    text-align: center; font-size: 9px; color: var(--ink);
  }
</style>
</head>
<body>
  <header class="site-header">
    <div class="brand"><span class="brand-dot"></span>HAULBRIX</div>
    <nav class="main-nav">
      <a href="#">Book</a>
      <a href="#">How It Works</a>
      <a href="#" class="nav-cta">Become a Driver</a>
      <a href="#" class="nav-account">sam@ternwello.com</a>
    </nav>
  </header>

  <section class="panel booking">
    <h2 class="panel-title">Booking Details</h2>
    <div class="booking-form">
      <div class="field field-package">
        <label>Package selected :</label>
        <div class="control">Package 1
          <svg width="10" height="6" viewBox="0 0 10 6"><path d="M0 0h10L5 6z" fill="#555"/></svg>
        </div>
      </div>
      <div class="field field-time">
        <label>Pick-up time selected :</label>
        <div class="control">July 18 at 4:13 am
          <svg width="14" height="14" viewBox="0 0 14 14" fill="none" stroke="#555" stroke-width="1.2">
            <rect x="1" y="2.5" width="12" height="10.5"/><path d="M1 5.5h12M4 1v3M10 1v3M4 8h1M7 8h1M10 8h1M4 10.5h1M7 10.5h1M10 10.5h1"/>
          </svg>
        </div>
      </div>
      <div class="field field-desc">
        <label>Description :</label>
        <div class="control">1 large stove</div>
      </div>
      <button class="btn-update">UPDATE</button>
    </div>
  </section>

  <section class="panel drivers">
    <h2 class="panel-title">Drivers in your area</h2>
    <div class="drivers-body">
      <p class="notice">Please stay on this page and be patient, while we contact the drivers and find you one ASAP.</p>
      <table class="driver-table">
        <thead>
          <tr><th class="col-name">Name</th><th class="col-distance">Distance (km)</th><th class="col-time">Agreed pick-up time</th><th></th></tr>
        </thead>
        <tbody>
          <tr><td>Dale Pruett</td><td>4.04km away</td><td>-</td><td><span class="status">Pending</span></td></tr>
          <tr><td>Owen Farlow</td><td>5.7km away</td><td>-</td><td><span class="status">Pending</span></td></tr>
          <tr><td>Ivan Roskel</td><td>11.13km away</td><td>-</td><td><span class="status">Pending</span></td></tr>
          <tr><td>Milo Brandt</td><td>11.91km away</td><td>-</td><td><span class="status">Pending</span></td></tr>
        </tbody>
      </table>
    </div>
  </section>

  <footer class="site-footer">Copyright &copy; 2017 Haulbrix. All rights reserved.</footer>
</body>
</html>
```